Business Card Design

New business card design

Target Market(s)

Residential & Commercial Property Managers

Industry/Entity Type

Plumbing Services

Contact Information for Business Card

Name - Rowan Keddle, title - Director, Phone Number - 0431 286 517, email - rowan@tbk-plumbing.com.au, Company ABN - 73 215 904 386,

Font styles to use
Sans Serif

Colors
0054AA
0677BA
7BADD7
CADEEF
E8F1F8

```html
<!DOCTYPE html>
<html lang="en">
<head>
<meta charset="utf-8">
<title>TBK Plumbing Services – Business Card</title>
<link rel="stylesheet" href="https://fonts.googleapis.com/css2?family=Montserrat:wght@400;500;700&display=swap">
<style>
  :root {
    --page-bg: #d9dcdf;
    --card-dark: #1e2329;
    --card-light: #ffffff;
    --ink: #1e2329;
    --ink-soft: #2b2f33;
    --accent: #3bb6e8;
    --accent-deep: #2a9fdc;
    --tagline: #6b5a52;
  }
  * { box-sizing: border-box; margin: 0; padding: 0; }
  html, body {
    width: 1200px;
    height: 880px;
    overflow: hidden;
    background: var(--page-bg);
    font-family: "Montserrat", sans-serif;
  }
  .canvas {
    position: relative;
    width: 1200px;
    height: 880px;
  }
  .card {
    position: absolute;
    left: 250px;
    width: 700px;
    height: 400px;
    border-radius: 32px;
    overflow: hidden;
    box-shadow: 0 8px 24px rgba(0,0,0,0.18);
  }
  /* Front */
  .card-front {
    top: 30px;
    background: var(--card-dark);
    display: flex;
    align-items: center;
    justify-content: center;
  }
  .wordmark {
    display: flex;
    align-items: center;
    gap: 18px;
  }
  .wordmark-dot {
    width: 22px;
    height: 22px;
    border-radius: 50%;
    background: currentColor;
  }
  .wordmark-name {
    font-weight: 500;
    letter-spacing: 0.06em;
    text-transform: lowercase;
  }
  .card-front .wordmark { color: #ffffff; }
  .card-front .wordmark-name { font-size: 46px; }

  /* Back */
  .card-back {
    top: 450px;
    background: var(--card-light);
  }
  .card-back .wordmark {
    position: absolute;
    left: 40px;
    top: 44px;
    color: var(--ink);
    gap: 12px;
  }
  .card-back .wordmark-name { font-size: 30px; }
  .card-back .wordmark-dot { width: 16px; height: 16px; }

  .identity {
    position: absolute;
    left: 0;
    top: 200px;
    display: flex;
    align-items: stretch;
  }
  .identity-bar {
    width: 34px;
    background: var(--accent);
  }
  .identity-text {
    padding-left: 18px;
  }
  .person-name {
    font-size: 30px;
    font-weight: 700;
    color: var(--accent-deep);
    line-height: 1.15;
  }
  .person-role {
    font-size: 22px;
    font-weight: 400;
    color: var(--ink-soft);
    line-height: 1.3;
  }
  .contacts {
    position: absolute;
    left: 52px;
    top: 296px;
    list-style: none;
  }
  .contact {
    display: flex;
    align-items: center;
    gap: 10px;
    font-size: 21px;
    color: var(--ink-soft);
    line-height: 1.55;
  }
  .contact svg { width: 20px; height: 20px; flex: none; }
  .abn {
    position: absolute;
    right: 40px;
    bottom: 112px;
    font-size: 19px;
    color: var(--ink-soft);
  }
</style>
</head>
<body>
<main class="canvas">
  <section class="card card-front" aria-label="Card front">
    <div class="wordmark">
      <span class="wordmark-dot"></span>
      <span class="wordmark-name">tbk plumbing services</span>
    </div>
  </section>

  <section class="card card-back" aria-label="Card back">
    <div class="wordmark">
      <span class="wordmark-dot"></span>
      <span class="wordmark-name">tbk plumbing services</span>
    </div>

    <div class="identity">
      <span class="identity-bar"></span>
      <div class="identity-text">
        <p class="person-name">Rowan Keddle</p>
        <p class="person-role">Director</p>
      </div>
    </div>

    <ul class="contacts">
      <li class="contact">
        <svg viewBox="0 0 24 24" aria-hidden="true"><path fill="#2a9fdc" d="M6.6 10.8a15.1 15.1 0 0 0 6.6 6.6l2.2-2.2a1 1 0 0 1 1-.25 11.4 11.4 0 0 0 3.6.57 1 1 0 0 1 1 1V20a1 1 0 0 1-1 1A17 17 0 0 1 3 4a1 1 0 0 1 1-1h3.5a1 1 0 0 1 1 1c0 1.25.2 2.45.57 3.57a1 1 0 0 1-.25 1z"/></svg>
        <span>0431 286 517</span>
      </li>
      <li class="contact">
        <svg viewBox="0 0 24 24" aria-hidden="true"><rect x="2" y="5" width="20" height="14" rx="2" fill="#2a9fdc"/><path d="M3 6.5l9 6.5 9-6.5" fill="none" stroke="#fff" stroke-width="1.6"/></svg>
        <span>rowan@tbk-plumbing.com.au</span>
      </li>
    </ul>

    <p class="abn">Company ABN - 73 215 904 386</p>
  </section>
</main>
</body>
</html>
```